Pipe Repair Clamps

A double side A4 showing our pipe repair clamps for stopping leaking pipes within seconds. For water , sewage companies, hotels, malls, airports, hosptals, facilities management companies and district cooling companies. Reverse side will show a size chart. Examples of product uploaded

```html
<!DOCTYPE html>
<html lang="en">
<head>
<meta charset="utf-8">
<title>Pipe Repair Clamps – Size Chart</title>
<link href="https://fonts.googleapis.com/css2?family=Open+Sans:wght@400;600;700;800&family=Roboto:wght@400&display=swap" rel="stylesheet">
<style>
  :root{
    --bg-top:#eeeff1;
    --bg-mid:#e6e3e0;
    --bg-low:#d9cfc6;
    --head:#b8531e;
    --row-alt:#e1ecda;
    --row:#ffffff;
    --rule:#3f8a3b;
    --blue:#1a8ad4;
    --steel:#4f82c0;
    --spec-head:#4b87c0;
    --spec-row:rgba(200,205,212,.55);
    --ink:#1d1d1d;
  }
  *{margin:0;padding:0;box-sizing:border-box}
  html,body{width:927px;height:1200px;overflow:hidden}
  body{font-family:"Open Sans",sans-serif;color:var(--ink)}
  .sheet{position:relative;width:927px;height:1200px;
    background:linear-gradient(180deg,var(--bg-top) 0%,var(--bg-mid) 55%,var(--bg-low) 78%,#cdbfb3 90%,#d8cfc7 100%)}
  .skyline{position:absolute;left:0;top:900px;width:927px;height:220px;
    background:linear-gradient(180deg,rgba(150,160,170,0) 0%,rgba(140,150,160,.45) 45%,rgba(170,160,150,.6) 80%,rgba(205,195,185,.3) 100%)}
  .size-chart{position:absolute;left:58px;top:50px;width:532px;border-collapse:collapse;table-layout:fixed;
    font-family:"Roboto",sans-serif;font-size:8px;text-align:center;border-bottom:2px solid var(--rule)}
  .size-chart th{background:var(--head);color:#fff;font-weight:400;font-size:7px;height:29px;line-height:10px}
  .size-chart td{height:17.3px;background:var(--row)}
  .size-chart tr:nth-child(even) td{background:var(--row-alt)}
  .note{position:absolute;left:64px;top:696px;font-size:7.5px;font-family:"Roboto",sans-serif}
  .photo{position:absolute;left:624px;top:0;width:268px;height:628px;
    background:linear-gradient(160deg,#5a5a5e 0%,#8a8070 35%,#4a4a4e 60%,#3a3f48 100%)}
  .label{position:absolute;color:var(--steel);font-weight:600;font-size:23px;text-align:center;line-height:29px}
  .leak{left:632px;top:672px;width:252px}
  .tape{left:632px;top:812px;width:252px}
  .tool-img{position:absolute;left:636px;top:740px;width:248px;height:52px;
    background:linear-gradient(170deg,rgba(120,125,130,0) 40%,rgba(120,125,130,.55) 50%,rgba(120,125,130,0) 60%)}
  .tape-img{position:absolute;left:656px;top:840px;width:228px;height:88px;border-radius:40px 44px 44px 10px;
    background:linear-gradient(180deg,#fbfbfb,#e2e2e2)}
  .hdpe{position:absolute;left:40px;top:740px;width:144px;text-align:right;color:var(--blue);
    font-weight:800;font-size:21px;line-height:27px}
  .arrow{position:absolute;left:196px;top:742px}
  .hdpe-img{position:absolute;left:94px;top:832px;width:110px;height:100px;border-radius:8px;
    background:linear-gradient(160deg,#6a6a6e,#2e2e32)}
  .spec{position:absolute;left:254px;top:740px;width:349px;border-collapse:collapse;font-size:11.5px}
  .spec th{background:var(--spec-head);color:#fff;font-weight:600;font-size:13.5px;height:26px}
  .spec td{background:var(--spec-row);height:21.8px;border-top:1px solid rgba(255,255,255,.35);text-align:center;width:50%}
  .spec td+td{border-left:1px solid rgba(255,255,255,.35)}
  .brand-name{position:absolute;left:92px;top:1108px;font-weight:600;font-size:17px;color:var(--ink);letter-spacing:.5px}
  .web{position:absolute;left:0;width:927px;text-align:center}
  .web-url{top:1132px;font-weight:800;font-size:20px;letter-spacing:.2px}
  .web-sub{top:1160px;font-weight:600;font-size:11.5px}
</style>
</head>
<body>
<div class="sheet">
  <div class="skyline" role="img" aria-label="City skyline photo fading into the background"></div>

  <table class="size-chart">
    <colgroup><col style="width:42px"><col style="width:82px"><col style="width:39px"><col style="width:41px"><col style="width:38px"><col style="width:24px"><col style="width:32px"><col style="width:84px"><col style="width:70px"><col style="width:36px"><col style="width:44px"></colgroup>
    <thead><tr><th>OD<br>(mm)</th><th>ODmin-ODmax<br>(mm)</th><th>PN<br>(mm)</th><th>WP<br>(bar)</th><th>C<br>(mm)</th><th>l1<br>(mm)</th><th>l2<br>(mm)</th><th>D<br>(mm)</th><th>H<br>(mm)</th><th>M</th><th>Nm</th></tr></thead>
    <tbody>
      <tr><td>21.7</td><td>21-23</td><td>16</td><td>32</td><td>3</td><td>57</td><td>–</td><td>35</td><td>50</td><td>6</td><td>15</td></tr>
      <tr><td>25</td><td>24.5-25.5</td><td>16</td><td>32</td><td>3</td><td>57</td><td>–</td><td>50</td><td>70</td><td>6</td><td>15</td></tr>
      <tr><td>27.2</td><td>26-28</td><td>16</td><td>32</td><td>3</td><td>57</td><td>–</td><td>50</td><td>70</td><td>6</td><td>15</td></tr>
      <tr><td>32</td><td>31.5-32.5</td><td>16</td><td>32</td><td>3</td><td>57</td><td>–</td><td>55</td><td>75</td><td>6</td><td>15</td></tr>
      <tr><td>34</td><td>33-35</td><td>16</td><td>32</td><td>3</td><td>57</td><td>–</td><td>55</td><td>75</td><td>6</td><td>15</td></tr>
      <tr><td>40</td><td>39.5-41.5</td><td>16</td><td>32</td><td>5</td><td>57</td><td>–</td><td>55</td><td>75</td><td>6</td><td>15</td></tr>
      <tr><td>42</td><td>42-44</td><td>16</td><td>32</td><td>5</td><td>57</td><td>–</td><td>65</td><td>85</td><td>6</td><td>15</td></tr>
      <tr><td>44.5</td><td>44-45.1</td><td>16</td><td>32</td><td>5</td><td>57</td><td>–</td><td>65</td><td>85</td><td>6</td><td>15</td></tr>
      <tr><td>48.6</td><td>47-49</td><td>16</td><td>32</td><td>5</td><td>57</td><td>100</td><td>70</td><td>90</td><td>6</td><td>15</td></tr>
      <tr><td>54</td><td>53.3-54.6</td><td>16</td><td>32</td><td>5</td><td>57</td><td>100</td><td>70</td><td>90</td><td>8</td><td>30</td></tr>
      <tr><td>57</td><td>56.3-57.7</td><td>16</td><td>32</td><td>5</td><td>57</td><td>100</td><td>50</td><td>100</td><td>8</td><td>30</td></tr>
      <tr><td>60.3</td><td>59-62</td><td>16</td><td>32</td><td>5</td><td>80</td><td>139</td><td>85</td><td>105</td><td>8</td><td>30</td></tr>
      <tr><td>63</td><td>62.2-63.9</td><td>16</td><td>32</td><td>5</td><td>80</td><td>139</td><td>85</td><td>105</td><td>8</td><td>30</td></tr>
      <tr><td>76.1</td><td>75-78</td><td>14</td><td>28</td><td>5</td><td>80</td><td>139</td><td>100</td><td>120</td><td>8</td><td>30</td></tr>
      <tr><td>79.9</td><td>78.8-80.8</td><td>14</td><td>28</td><td>5</td><td>80</td><td>139</td><td>100</td><td>120</td><td>8</td><td>30</td></tr>
      <tr><td>88.9</td><td>88-92</td><td>14</td><td>28</td><td>5</td><td>107</td><td>203</td><td>110</td><td>130</td><td>10</td><td>50</td></tr>
      <tr><td>108</td><td>106-110</td><td>14</td><td>28</td><td>5</td><td>107</td><td>203</td><td>130</td><td>150</td><td>10</td><td>50</td></tr>
      <tr><td>110</td><td>108.9-111.2</td><td>14</td><td>28</td><td>5</td><td>107</td><td>203</td><td>130</td><td>150</td><td>10</td><td>50</td></tr>
      <tr><td>114.3</td><td>112-116</td><td>14</td><td>28</td><td>5</td><td>107</td><td>203</td><td>135</td><td>155</td><td>10</td><td>50</td></tr>
      <tr><td>118</td><td>116.6-119.2</td><td>14</td><td>28</td><td>5</td><td>107</td><td>203</td><td>140</td><td>160</td><td>10</td><td>50</td></tr>
      <tr><td>125</td><td>12.6-126.5</td><td>14</td><td>28</td><td>5</td><td>107</td><td>203</td><td>150</td><td>185</td><td>10</td><td>50</td></tr>
      <tr><td>133</td><td>131.5-134.4</td><td>14</td><td>28</td><td>5</td><td>107</td><td>203</td><td>160</td><td>190</td><td>10</td><td>50</td></tr>
      <tr><td>140</td><td>137-143</td><td>14</td><td>28</td><td>5</td><td>116</td><td>203</td><td>165</td><td>195</td><td>12</td><td>80</td></tr>
      <tr><td>159</td><td>157-161</td><td>12</td><td>24</td><td>10</td><td>116</td><td>203</td><td>185</td><td>215</td><td>12</td><td>80</td></tr>
      <tr><td>165.2</td><td>163.3-166.7</td><td>12</td><td>24</td><td>10</td><td>116</td><td>203</td><td>190</td><td>210</td><td>12</td><td>80</td></tr>
      <tr><td>168</td><td>166-170</td><td>12</td><td>24</td><td>10</td><td>116</td><td>203</td><td>195</td><td>225</td><td>12</td><td>80</td></tr>
      <tr><td>170</td><td>168.2-171.9</td><td>12</td><td>24</td><td>10</td><td>116</td><td>203</td><td>195</td><td>225</td><td>14</td><td>100</td></tr>
      <tr><td>200</td><td>198.2-201.5</td><td>8</td><td>16</td><td>10</td><td>116</td><td>203</td><td>240</td><td>270</td><td>14</td><td>100</td></tr>
      <tr><td>219</td><td>217-221</td><td>8</td><td>16</td><td>10</td><td>155</td><td>255</td><td>250</td><td>280</td><td>14</td><td>100</td></tr>
      <tr><td>250</td><td>250-254</td><td>8</td><td>16</td><td>10</td><td>155</td><td>255</td><td>285</td><td>315</td><td>14</td><td>100</td></tr>
      <tr><td>273</td><td>271-275</td><td>8</td><td>16</td><td>10</td><td>155</td><td>255</td><td>305</td><td>335</td><td>14</td><td>100</td></tr>
      <tr><td>315</td><td>313-317</td><td>7</td><td>14</td><td>10</td><td>155</td><td>255</td><td>340</td><td>375</td><td>14</td><td>100</td></tr>
      <tr><td>325</td><td>323-327</td><td>7</td><td>14</td><td>10</td><td>155</td><td>255</td><td>360</td><td>390</td><td>14</td><td>100</td></tr>
      <tr><td>355.6</td><td>354-358</td><td>7</td><td>14</td><td>10</td><td>155</td><td>255</td><td>385</td><td>420</td><td>14</td><td>100</td></tr>
      <tr><td>377</td><td>375-379</td><td>7</td><td>14</td><td>10</td><td>155</td><td>255</td><td>410</td><td>440</td><td>14</td><td>100</td></tr>
    </tbody>
  </table>
  <p class="note">Some sizes and lengths not listed are avaliable upon request.</p>

  <div class="photo" role="img" aria-label="Photo of a gloved hand fitting a blue repair clamp over a pipe spraying water"></div>

  <div class="label leak">LEAK<br>DETECTION TOOL</div>
  <div class="tool-img" role="img" aria-label="Photo of a leak detection listening rod"></div>
  <div class="label tape">PIPE O.D. TAPE</div>
  <div class="tape-img" role="img" aria-label="Photo of a white pipe diameter measuring tape"></div>

  <div class="hdpe">HDPE<br>REPAIR<br>SECTION</div>
  <svg class="arrow" width="36" height="28" viewBox="0 0 36 28" aria-hidden="true">
    <path d="M2 14H30M20 4L31 14L20 24" fill="none" stroke="#1a8ad4" stroke-width="4.5" stroke-linecap="round" stroke-linejoin="round"/>
  </svg>
  <div class="hdpe-img" role="img" aria-label="Photo of a black HDPE split repair section"></div>

  <table class="spec">
    <thead><tr><th colspan="2">SPECIFICATION</th></tr></thead>
    <tbody>
      <tr><td>DN40MM</td><td>DN200MM</td></tr>
      <tr><td>DN50MM</td><td>DN225MM</td></tr>
      <tr><td>DN63MM</td><td>DN250MM</td></tr>
      <tr><td>DN75MM</td><td>DN280MM</td></tr>
      <tr><td>DN90MM</td><td>DN315MM</td></tr>
      <tr><td>DN110MM</td><td>DN355MM</td></tr>
      <tr><td>DN125MM</td><td>DN400MM</td></tr>
      <tr><td>DN140MM</td><td>DN450MM</td></tr>
      <tr><td>DN160MM</td><td>DN500MM</td></tr>
      <tr><td>DN180MM</td><td>DN630MM</td></tr>
    </tbody>
  </table>

  <p class="brand-name">Keystone</p>

  <p class="web web-url">WWW.KEYSTONEPIPEFITTINGS.COM</p>
  <p class="web web-sub">A MARROWFIELD GROUP COMPANY</p>
</div>
</body>
</html>
```